Harbor Seal Works Spray Foam Appications website

We need a custom website for our company, www.harborsealworks.example. We need something we can modify by adding/changing content, photos, updated projects, etc. We are a commercial contractor specializing in Spray Foam applications. We want the website to be very creative and easy to navigate. The main points of the website are to showcase our projects, and describe our scope of services. We provide spray foam applications to the residential and commercial market. We offer Spray Foam roofing applications, as well as Spray Foam interior insulation applications. We also provide Roof Restoration Coating Systems to refurbish old and failing metal roofs. We would be ok with a one page web design if we can get the scope of our services to flow in a single page. The designer can decide if single or multiple pages works best for our business. One of the suppliers we work with is www.verdansupply.example.

Target Market(s)

Residential Home Builders, General Contractors, Commercial Construction Companies, Property Management Groups.

Industry/Entity Type

Insulation

Number of Pages Required

5+ page

Font styles to use
Serif
Sans Serif

Colors

Designer to choose colors to be used in the design.

Requirements
Must have
• We already have a Wix page, so website must be a Wix theme design. Nice easy to navigate format. Color matched to our current logo theme. We already have brochures and would like for it to match what's already in the hands of some of our customers. Need to be able to manage content to update photos, projects, scope of service, etc., via Wix. Current hold/splash page is hosted at www.harborsealworks.example. We would also like to have this video posted on the home page: https://www.videohost.example/watch?v=QxT4pLm9ZrA&feature=share
Nice to have
• I have attached some splash videos, being able to incorporate these somehow without being overpowering would be nice.

```html
<!DOCTYPE html>
<html lang="en">
<head>
<meta charset="utf-8">
<title>Harbor Seal Works – Spray Foam Applications</title>
<link href="https://fonts.googleapis.com/css2?family=Roboto:ital,wght@0,300;0,400;0,500;0,700;1,400;1,700&display=swap" rel="stylesheet">
<style>
:root{
  --yellow:#f2ae1c;
  --yellow-dark:#e09f12;
  --ink:#222;
  --text:#444;
  --muted:#9a9a9a;
  --dark:#2f2f2f;
  --darker:#242424;
  --footer:#2b2b2b;
  --light:#f3f3f3;
  --white:#fff;
  --line:#e6e6e6;
}
*{margin:0;padding:0;box-sizing:border-box}
html,body{width:1200px;height:3746px;overflow:hidden}
body{position:relative;font-family:'Roboto',sans-serif;color:var(--text);background:var(--white)}
.abs{position:absolute}
a{color:inherit;text-decoration:none}

/* header */
.site-header{position:absolute;left:0;top:0;width:1200px;height:90px;background:var(--white)}
.brand{position:absolute;left:160px;top:26px;display:flex;align-items:center;gap:10px}
.brand-mark{width:34px;height:34px;border:3px solid var(--yellow);border-radius:50%}
.brand-name{font-size:15px;font-weight:500;color:var(--yellow);letter-spacing:.5px;text-transform:uppercase}
.main-nav{position:absolute;top:38px;left:391px;display:flex;gap:0;font-size:11.5px;font-weight:500;color:#333}
.main-nav a{position:absolute;white-space:nowrap}
.main-nav .active{color:var(--yellow)}
.btn{display:inline-flex;align-items:center;justify-content:center;background:var(--yellow);color:var(--white);font-size:10.5px;font-weight:700;text-transform:uppercase;letter-spacing:.3px}
.quote-btn{position:absolute;left:900px;top:22px;width:137px;height:45px}

/* hero */
.hero{position:absolute;left:0;top:90px;width:1200px;height:435px;background:var(--dark)}
.hero-photo{position:absolute;left:0;top:0;width:1200px;height:185px;background:linear-gradient(180deg,#3a3a3a,#4a4a4a 60%,#444)}
.hero-strip{position:absolute;left:0;top:350px;width:1200px;height:85px;background:linear-gradient(90deg,#4a4a4a,#3d3d3d 50%,#4b4b4b)}
.hero h1{position:absolute;left:0;top:112px;width:1200px;text-align:center;font-size:29px;font-weight:500;color:var(--white)}
.hero h1 em{display:block;font-size:30px;font-weight:700;color:var(--yellow);margin-top:4px}
.hero p{position:absolute;left:300px;top:207px;width:600px;text-align:center;font-size:10.5px;line-height:22px;font-style:italic;font-weight:500;color:var(--white)}
.hero .btn{position:absolute;left:545px;top:278px;width:110px;height:37px}
.dots{position:absolute;left:1025px;top:180px}
.dots span{display:block;width:8px;height:8px;border-radius:50%;background:var(--white);margin-bottom:11px}
.dots .on{background:var(--yellow);width:12px;height:12px;margin-left:-2px;border:2px solid #ddd}

/* feature cards */
.features{position:absolute;left:160px;top:466px;width:877px;height:292px;display:flex;background:var(--white)}
.feature{flex:1;text-align:center;padding-top:45px;box-shadow:0 4px 18px rgba(0,0,0,.07)}
.feature-icon{width:60px;height:60px;margin:0 auto;border:1px solid var(--yellow);display:flex;align-items:center;justify-content:center}
.feature-icon.filled{background:var(--yellow)}
.feature h3{font-size:14.5px;font-weight:500;color:var(--ink);margin-top:30px;text-transform:uppercase}
.feature .rule{width:22px;height:2px;background:var(--yellow);margin:11px auto 14px;opacity:.6}
.feature p{font-size:10px;line-height:22px;color:#aaa;padding:0 20px}
.feature .more{display:block;margin-top:22px;font-size:10px;font-weight:500;color:#888;text-transform:uppercase}
.feature .more.hl{color:var(--yellow)}

/* section headings */
.eyebrow{font-size:7.5px;letter-spacing:1px;color:#aaa;text-transform:uppercase}
.sec-head{position:absolute;padding-left:14px;border-left:3px solid var(--yellow)}
.sec-head h2{font-size:19px;font-weight:500;color:var(--ink);margin-top:5px}

/* about */
.ph{position:absolute}
.about-back{left:160px;top:818px;width:264px;height:187px;background:linear-gradient(135deg,#c9c3b4,#e8e3d6 50%,#9f9a8e)}
.about-card{position:absolute;left:235px;top:920px;width:353px;height:308px;background:var(--white);box-shadow:0 4px 16px rgba(0,0,0,.12)}
.about-video{left:10px;top:10px;width:336px;height:288px;background:linear-gradient(180deg,#4d6a8a 0%,#8c8a80 30%,#9b8c63 60%,#c9b47a 100%)}
.play{position:absolute;left:117px;top:108px;width:60px;height:60px;border-radius:50%;background:var(--yellow);box-shadow:0 0 0 6px rgba(242,174,28,.35);display:flex;align-items:center;justify-content:center}
.watch{position:absolute;left:188px;top:132px;font-size:8px;font-style:italic;color:var(--white);text-decoration:underline}
.about-copy{position:absolute;left:611px;top:870px;width:427px}
.about-copy p{font-size:10px;line-height:22.5px;color:#777}
.about-copy p.lead{color:#999}
.about-copy p+p{margin-top:14px}
.text-link{display:inline-flex;align-items:center;gap:8px;font-size:10px;font-weight:500;color:var(--yellow);text-transform:uppercase}
.about-rule{position:absolute;left:611px;top:1145px;width:427px;height:1px;background:var(--line)}
.perks{position:absolute;left:611px;top:1172px;width:427px;display:flex;justify-content:space-between}
.perk{display:flex;align-items:center;gap:10px;font-size:10px;line-height:15px;color:#333}

/* services */
.services-band{position:absolute;left:0;top:1333px;width:648px;height:490px;background:var(--yellow)}
.services-photo{left:648px;top:1290px;width:552px;height:533px;background:linear-gradient(160deg,#d9d2c0,#b9ad98 45%,#8c8474)}
.services-band .sec-head{left:160px;top:60px;border-color:var(--white)}
.services-band .eyebrow{color:#fff3d6}
.services-band h2{color:var(--white)}
.services-band .intro{position:absolute;left:160px;top:130px;width:440px;font-size:9.5px;font-weight:700;line-height:22px;color:var(--white)}
.service{position:absolute;left:160px;width:422px}
.service-icon{position:absolute;left:0;top:0;width:45px;height:43px;border:1px solid var(--white);display:flex;align-items:center;justify-content:center}
.service h4{position:absolute;left:61px;top:0;font-size:11.5px;font-weight:700;color:var(--white)}
.service p{position:absolute;left:61px;top:22px;width:360px;font-size:9.5px;line-height:18px;color:var(--white)}
.services-rule{position:absolute;left:160px;top:294px;width:422px;height:1px;background:rgba(255,255,255,.55)}
.view-all{position:absolute;left:160px;top:421px;color:var(--white)}

/* testimonial */
.testimonial{position:absolute;left:0;top:1823px;width:1200px;height:426px;background:var(--dark)}
.worker-photo{left:160px;top:1823px;width:353px;height:487px;background:linear-gradient(150deg,#d6a520 0%,#6b5a3a 35%,#2d3540 70%,#3b4552)}
.avatar{position:absolute;left:575px;top:61px;width:72px;height:72px;border-radius:50%;border:3px solid var(--yellow);background:#d8d8d8}
.arrows{position:absolute;left:926px;top:58px;display:flex;gap:8px}
.client{position:absolute;left:574px;top:146px;font-size:11px;font-weight:700;font-style:italic;color:var(--white)}
.quote{position:absolute;left:574px;top:177px;width:410px;padding-left:16px;border-left:2px solid var(--yellow);font-size:9.5px;font-style:italic;line-height:22.5px;color:#aaa}
.stats{position:absolute;left:574px;top:300px;width:400px;display:flex}
.stat{width:146px;text-align:center}
.stat .num{display:flex;align-items:center;justify-content:center;gap:8px;font-size:26px;color:var(--yellow);font-weight:400}
.stat .lbl{margin-top:18px;font-size:9.5px;color:#ccc;text-transform:uppercase}

/* projects */
.filters{position:absolute;top:2404px;right:163px;display:flex;gap:22px;font-size:10px;color:#444;text-transform:uppercase}
.filters .on{color:var(--yellow);text-decoration:underline}
.project{position:absolute;width:277px;height:188px}
.p1{left:160px;top:2459px;background:linear-gradient(180deg,#5a5a5a,#6e6a64)}
.p2{left:461px;top:2459px;background:linear-gradient(180deg,#b7a98f,#e2ddd0 60%,#9a9a98)}
.p3{left:760px;top:2459px;background:linear-gradient(180deg,#3f65a8,#7a9ac8 45%,#c8ccd2 55%,#9aa0a8)}
.p4{left:160px;top:2669px;background:linear-gradient(180deg,#8da0b5,#6e6f66 40%,#cfcfcf 60%,#eee)}
.p5{left:461px;top:2669px;background:linear-gradient(180deg,#2f66c0,#8fb1d8 40%,#c7b98a 55%,#e6d7a2)}
.p6{left:760px;top:2669px;background:linear-gradient(180deg,#c7cdd4,#e8eaec 40%,#c9cbce)}
.project-overlay{position:absolute;inset:0;background:rgba(40,40,40,.55)}
.project-frame{position:absolute;left:15px;top:15px;right:15px;bottom:15px;border:1px solid rgba(255,255,255,.6);text-align:center;padding-top:46px}
.project-frame .cat{font-size:10px;color:var(--white);letter-spacing:1px;text-transform:uppercase}
.project-frame .title{font-size:14px;color:var(--yellow);margin-top:6px}
.project-frame .bar{width:36px;height:3px;background:var(--yellow);margin:16px auto 0}

/* blog */
.blog{position:absolute;left:0;top:2917px;width:1200px;height:526px;background:var(--light)}
.blog .btn{position:absolute;left:929px;top:61px;width:108px;height:44px}
.post{position:absolute;width:277px;background:var(--white);padding:11px}
.post .thumb{height:135px}
.post .date{display:flex;align-items:center;gap:6px;margin:22px 0 0 8px;font-size:7.5px;font-style:italic;color:#bbb}
.post h5{margin:10px 0 0 8px;font-size:11.5px;font-weight:400;line-height:22.5px;color:#333}
.post.featured h5{color:var(--yellow)}

/* footer */
.site-footer{position:absolute;left:0;top:3443px;width:1200px;height:255px;background:var(--footer);color:#ddd}
.site-footer .brand{top:50px}
.foot-about{position:absolute;left:160px;top:117px;width:205px;font-size:9.5px;line-height:15px;color:#ddd}
.follow{position:absolute;left:160px;top:202px;display:flex;align-items:center;gap:12px;font-size:9px;color:var(--yellow);text-transform:uppercase}
.follow i{display:block;width:6px;height:6px;background:var(--white)}
.foot-title{position:absolute;top:56px;font-size:14px;font-weight:700;color:var(--white);text-transform:uppercase}
.quick{position:absolute;left:385px;top:111px;font-size:9.5px;color:#ddd}
.quick a{position:absolute;white-space:nowrap;text-transform:uppercase}
.quick .on{color:var(--yellow);text-decoration:underline}
.news{position:absolute;left:613px;top:111px;width:200px;font-size:9.5px;line-height:15px}
.news p+p{margin-top:22px;padding-top:0}
.news hr{border:0;border-top:1px solid #555;margin:9px 0 12px}
.contact{position:absolute;left:837px;top:111px;font-size:9.5px;line-height:15px}
.contact .k{color:var(--yellow)}
.contact .k:not(:first-child){margin-top:6px}
.copyright{position:absolute;left:0;top:3698px;width:1200px;height:48px;background:var(--darker);text-align:center;line-height:48px;font-size:9px;color:#ddd}
.copyright em{color:var(--yellow)}
</style>
</head>
<body>

<header class="site-header">
  <div class="brand"><span class="brand-mark"></span><span class="brand-name">Harbor Seal Works</span></div>
  <nav class="main-nav">
    <a class="active" style="left:0">HOME</a>
    <a style="left:64px">ABOUT US</a>
    <a style="left:151px">SERVICES</a>
    <a style="left:236px">WORK</a>
    <a style="left:299px">BLOG</a>
    <a style="left:359px">CONTACT US</a>
  </nav>
  <a class="btn quote-btn">Request a quote</a>
</header>

<section class="hero">
  <div class="hero-photo" role="img" aria-label="Crew of spray foam workers standing on a commercial roof"></div>
  <div class="hero-strip" role="img" aria-label="Continuation of the rooftop crew photograph"></div>
  <h1>We Are The Undisputed Leaders<em>IN THIS INDUSTRY!</em></h1>
  <p>Lorem ipsum dolor amet 3 wolf moon unicorn selfies bitters keffiyeh c squid edison bulb synth roof party palo santo you probably haven't heard of them lo-fi. Raw denim cardigan before they could if and andy sold out four loko kombucha, YOLO</p>
  <a class="btn">Learn more</a>
  <div class="dots"><span></span><span class="on"></span><span></span></div>
</section>

<section class="features">
  <div class="feature">
    <div class="feature-icon"><svg width="22" height="22" viewBox="0 0 24 24" fill="none" stroke="#f2ae1c" stroke-width="1.3"><circle cx="12" cy="12" r="3.5"/><path d="M12 2v3M12 19v3M2 12h3M19 12h3M4.9 4.9l2.1 2.1M17 17l2.1 2.1M4.9 19.1L7 17M17 7l2.1-2.1"/></svg></div>
    <h3>Highly Experience</h3><div class="rule"></div>
    <p>Lorem ipsum dolor amet pBR&amp;B vinyl vaporware selvage man braid asymmetrical, hoodie wayfarers fo</p>
    <a class="more">More about</a>
  </div>
  <div class="feature">
    <div class="feature-icon filled"><svg width="30" height="22" viewBox="0 0 30 22" fill="none" stroke="#fff" stroke-width="1.3"><rect x="2" y="4" width="18" height="7"/><path d="M20 6h8M6 11v8h4v-8M13 11v4"/></svg></div>
    <h3>Many Services Provided</h3><div class="rule"></div>
    <p>Lorem ipsum dolor amet pBR&amp;B vinyl vaporware selvage man braid asymmetrical, hoodie wayfarers fo</p>
    <a class="more hl">More services</a>
  </div>
  <div class="feature">
    <div class="feature-icon"><svg width="30" height="22" viewBox="0 0 30 22" fill="none" stroke="#f2ae1c" stroke-width="1.3"><circle cx="9" cy="8" r="3"/><circle cx="21" cy="8" r="3"/><path d="M3 19c0-4 3-6 6-6s6 2 6 6M15 19c0-4 3-6 6-6s6 2 6 6"/></svg></div>
    <h3>Grateful Costumers</h3><div class="rule"></div>
    <p>Lorem ipsum dolor amet pBR&amp;B vinyl vaporware selvage man braid asymmetrical, hoodie wayfarers fo</p>
    <a class="more">Read more</a>
  </div>
</section>

<div class="ph about-back" role="img" aria-label="Worker in protective suit spraying foam insulation"></div>
<div class="about-card">
  <div class="ph about-video" role="img" aria-label="Video still of a coated metal warehouse roof">
    <span class="play"><svg width="18" height="20" viewBox="0 0 18 20"><path d="M2 1l15 9-15 9z" fill="#fff"/></svg></span>
    <span class="watch">Watch Video</span>
  </div>
</div>
<div class="sec-head" style="left:611px;top:820px">
  <div class="eyebrow">About Harbor Seal Works</div>
  <h2>We Are Here To Make Things Easier</h2>
</div>
<div class="about-copy" style="top:886px">
  <p class="lead">Lorem ipsum dolor amet pBR&amp;B vinyl vaporware selvage man braid asymmetrical, hoodie wayfarers YOLO aesthetic waistcoat tote bag ethical kale chips. Umami keytar church-key woke, cornhole ramps disrupt listicle. Vexillologist plaid 90's fanny pack</p>
  <p>Tattooed next level adaptogen, hella occupy aesthetic tofu locavore PBR&amp;B lomo. Narwhal celiac craft beer mlkshk ramps master cleanse. DIY lyft lumbersexual, twee unicorn jean shorts asymmetrical you probably haven't heard of them. Mustache mixtape roof party prism. Godard lyft seitan, lo-fi chicharrones succulents lumbersexual scenester if any lomo farm-to-table taiyaki</p>
  <p style="margin-top:20px"><a class="text-link">More about us <svg width="22" height="8" viewBox="0 0 22 8" fill="none" stroke="#f2ae1c"><path d="M0 4h20M17 1l3 3-3 3"/></svg></a></p>
</div>
<div class="about-rule"></div>
<div class="perks">
  <div class="perk"><svg width="24" height="24" viewBox="0 0 24 24" fill="none" stroke="#f2ae1c" stroke-width="1.3"><circle cx="12" cy="12" r="10"/><path d="M12 6v6l-4 3"/></svg><span>On-time<br>Services</span></div>
  <div class="perk"><svg width="24" height="24" viewBox="0 0 24 24" fill="none" stroke="#f2ae1c" stroke-width="1.3"><rect x="2" y="4" width="20" height="17"/><path d="M2 9h20M7 2v4M17 2v4M6 13h3v5H6zM11 13h3v5h-3zM16 13h3v5h-3z"/></svg><span>Certified<br>Professionals</span></div>
  <div class="perk"><svg width="24" height="24" viewBox="0 0 24 24" fill="none" stroke="#f2ae1c" stroke-width="1.3"><path d="M4 14v-2a8 8 0 0116 0v2"/><rect x="2" y="13" width="4" height="6" rx="1"/><rect x="18" y="13" width="4" height="6" rx="1"/><path d="M20 19c0 2-3 3-6 3"/></svg><span>24/7<br>Support</span></div>
</div>

<section class="services-band">
  <div class="sec-head">
    <div class="eyebrow">Working with excellence</div>
    <h2>Some Of Our Special Services</h2>
  </div>
  <p class="intro">Lorem ipsum dolor amet pBR&amp;B vinyl vaporware selvage man braid asymmetrical, hoodie ,wayfarers YOLO aesthetic waistcoat tote bag ethical kale chips. Umami keytar church-key woke</p>
  <div class="service" style="top:199px">
    <div class="service-icon"><svg width="26" height="16" viewBox="0 0 26 16" fill="none" stroke="#fff" stroke-width="1.1"><path d="M5 2h16l3 12H2zM9 2l-2 12M13 2v12M17 2l2 12M3.5 8h19"/></svg></div>
    <h4>Lorem Ipsum Roof Service</h4>
    <p>Tattooed next level adaptogen, hella occupy aesthetic tofu locavore PBR&amp;B lomo. Narwhal celiac craft beer mlkshk ramps master cleanse. DIY lyft lumbersexual, .twee unicorn jean shorts asymmetrical you probably haven't heard of th</p>
  </div>
  <div class="services-rule"></div>
  <div class="service" style="top:319px">
    <div class="service-icon"><svg width="26" height="20" viewBox="0 0 30 22" fill="none" stroke="#fff" stroke-width="1.3"><rect x="2" y="4" width="18" height="7"/><path d="M20 6h8M6 11v8h4v-8M13 11v4"/></svg></div>
    <h4>Lorem Ipsum Foam Service</h4>
    <p>Tattooed next level adaptogen, hella occupy aesthetic tofu locavore PBR&amp;B lomo. Narwhal celiac craft beer mlkshk ramps master cleanse. DIY lyft lumbersexual, .twee unicorn jean shorts asymmetrical you probably haven't heard of th</p>
  </div>
  <a class="text-link view-all">View all <svg width="22" height="8" viewBox="0 0 22 8" fill="none" stroke="#fff"><path d="M0 4h20M17 1l3 3-3 3"/></svg></a>
</section>
<div class="ph services-photo" role="img" aria-label="Technician spraying foam insulation onto attic rafters"></div>

<section class="testimonial">
  <div class="avatar" role="img" aria-label="Client portrait"></div>
  <div class="arrows">
    <svg width="16" height="10" viewBox="0 0 16 10" fill="none" stroke="#f2ae1c"><path d="M16 5H2M5 1L1 5l4 4"/></svg>
    <svg width="16" height="10" viewBox="0 0 16 10" fill="none" stroke="#f2ae1c"><path d="M0 5h14M11 1l4 4-4 4"/></svg>
  </div>
  <div class="client">Leon Varga - Costumer</div>
  <p class="quote">Lorem ipsum dolor amet vaporware snackwave intelligentsia meh, selvage shoreditch semiotics. Kombucha bicycle rights selvage, hoodie wolf marfa kogi man braid pok pok craft beer PBR&amp;B fashion axe quinoa. Drinking vinegar literally banh mi, salvia roof party slow-carb typewriter thundercats pour-over yr fam four loko humblebrag art party</p>
  <div class="stats">
    <div class="stat"><div class="num"><svg width="30" height="24" viewBox="0 0 30 24" fill="none" stroke="#f2ae1c" stroke-width="1.3"><rect x="2" y="6" width="26" height="16"/><path d="M11 6V2h8v4M2 12l13 5 13-5"/></svg>400+</div><div class="lbl">Projects done</div></div>
    <div class="stat"><div class="num"><svg width="22" height="26" viewBox="0 0 22 26" fill="none" stroke="#f2ae1c" stroke-width="1.3"><rect x="2" y="2" width="18" height="22"/><path d="M2 8h18M6 13h10M6 17h10M6 21h6"/></svg>200+</div><div class="lbl">Completed work</div></div>
    <div class="stat"><div class="num"><svg width="18" height="26" viewBox="0 0 18 26" fill="none" stroke="#f2ae1c" stroke-width="1.3"><circle cx="9" cy="8" r="6"/><path d="M5 13l-2 11 6-3 6 3-2-11"/></svg>20+</div><div class="lbl">Awards won</div></div>
  </div>
</section>
<div class="ph worker-photo" role="img" aria-label="Smiling construction worker in hard hat holding a clipboard"></div>

<div class="sec-head" style="left:160px;top:2370px">
  <div class="eyebrow">Recent work done</div>
  <h2>Recent Projects Done</h2>
</div>
<nav class="filters"><a class="on">All</a><a>Spray foam</a><a>Roof repair</a><a>Lorem</a><a>Ipsum</a></nav>
<div class="project p1" role="img" aria-label="Warehouse exterior after spray foam application">
  <div class="project-overlay"></div>
  <div class="project-frame"><div class="cat">Spray foam</div><div class="title">Lorem Ipsum Repair</div><div class="bar"></div></div>
</div>
<div class="project p2" role="img" aria-label="Interior walls insulated with spray foam"></div>
<div class="project p3" role="img" aria-label="Restored standing seam metal roof"></div>
<div class="project p4" role="img" aria-label="Coated commercial roof at dusk"></div>
<div class="project p5" role="img" aria-label="Freshly foamed roof with a safety cone"></div>
<div class="project p6" role="img" aria-label="White coated roof under overcast sky"></div>

<section class="blog">
  <div class="sec-head" style="left:160px;top:60px">
    <div class="eyebrow">Latest news</div>
    <h2>Recent Blog Posts</h2>
  </div>
  <a class="btn">Read all</a>
  <article class="post" style="left:160px;top:143px">
    <div class="thumb" role="img" aria-label="Workers at a colourful construction site" style="background:linear-gradient(135deg,#8a5a2a,#c79a3a 40%,#b23a2a 70%,#6a6a6a)"></div>
    <div class="date"><svg width="9" height="9" viewBox="0 0 10 10" fill="none" stroke="#bbb"><rect x="1" y="2" width="8" height="7"/><path d="M1 4h8"/></svg>January 2020</div>
    <h5>Tattooed next level adaptogen, hella most occupy aesthetic tofu locavore PBR&amp;B</h5>
  </article>
  <article class="post featured" style="left:461px;top:151px">
    <div class="thumb" role="img" aria-label="Installer spraying foam between wall studs" style="background:linear-gradient(90deg,#e7e1d4,#b9b2a2 40%,#e6e0d3 70%,#9c968b)"></div>
    <div class="date"><svg width="9" height="9" viewBox="0 0 10 10" fill="none" stroke="#bbb"><rect x="1" y="2" width="8" height="7"/><path d="M1 4h8"/></svg>January 2020</div>
    <h5>Tattooed next level adaptogen, hella most occupy aesthetic tofu locavore PBR&amp;B</h5>
  </article>
  <article class="post" style="left:760px;top:151px">
    <div class="thumb" role="img" aria-label="Attic rafters covered in spray foam" style="background:linear-gradient(180deg,#ece4cf,#cdbf9e 50%,#8a7255)"></div>
    <div class="date"><svg width="9" height="9" viewBox="0 0 10 10" fill="none" stroke="#bbb"><rect x="1" y="2" width="8" height="7"/><path d="M1 4h8"/></svg>January 2020</div>
    <h5>Tattooed next level adaptogen, hella most occupy aesthetic tofu locavore PBR&amp;B</h5>
  </article>
</section>

<footer class="site-footer">
  <div class="brand"><span class="brand-mark"></span><span class="brand-name">Harbor Seal Works</span></div>
  <p class="foot-about">Lorem ipsum dolor amet taxidermy poke knausgaard, next level adaptogen franzen leggings banh mi woke you probably haven't heard of them hell of vexillologist prism</p>
  <div class="follow">Follow us <i></i><i></i><i></i><i></i></div>
  <div class="foot-title" style="left:385px">Quick links</div>
  <div class="quick">
    <a class="on" style="left:0;top:0">Home</a><a style="left:77px;top:0">Services</a><a style="left:170px;top:0">About</a>
    <a style="left:0;top:22px">Blog</a><a style="left:88px;top:22px">Faqs</a><a style="left:167px;top:22px">Why ys</a>
    <a style="left:0;top:44px">Contact</a><a style="left:86px;top:44px">Work</a><a style="left:170px;top:44px">About</a>
  </div>
  <div class="foot-title" style="left:613px">Some news</div>
  <div class="news">
    <p>Aenean tristique justo et nibh molestie, non porttitor eros suscipit</p>
    <hr>
    <p style="margin-top:0">Aenean tristique justo et nibh molestie, non porttitor eros suscipit</p>
  </div>
  <div class="foot-title" style="left:837px">Contact us</div>
  <div class="contact">
    <div class="k">Address</div><div>Avenue 17 - IL 23 Street of Lorem Ipsum ,9433</div>
    <div class="k">E-mail</div><div>hello@harborsealworks.example</div>
    <div class="k">Phone Number</div><div>+1 23 456 789</div>
  </div>
</footer>
<div class="copyright"><em>HarborSealWorks 2020</em> - All Rights Reserved</div>

</body>
</html>
```